New B2C website design to help dads be better dads

DadHarbor is a website to help dads be the “best dad you can be.”

We require our website to be designed into a PSD format, no coding necessary.

The general concept is a two-page design. The first page is the login page, the second page is the home page. Once at the home page, rather than navigating to and from different pages, the user will push and pull through different visual and functional layers of the hierarchy. In theory, this should add to the user experience by having a visual anchor of where they are (through layered pagination) as well as improving loading times since the new information should only be a delta in data load versus a brand new page load.

The general look-and-feel we are going for is clean, simple, minimal. This means that the winning design will show us a good eye for web-optimized typography, good use of white (negative) space, and good use of a visually pleasing grid.

We require a total of 6 page "views" plus the landing page. We note that many of the views are similar to one another.
Landing page
Milestone view
Task view
Content view, articles
Content view, products
Search view
What's new view

Please review all of the additional information provided as well as the attachments for examples.

We provide the following websites as good references for:

Typography:
http://example-kelvorn.com/journal/

Use of white space:
http://www.trenvaskit.com/
http://moldrefin.com/

Example for “scrolling” page concept as well as good balance of color, typography, and white space:
http://www.qorbitalmeet.eu/

Please contact us with questions so that we can guide your design effort.
Updates

Hello designers,

The following information is added to help guide the design process:

1.  For the text dialogue below the landing page, please assume the following word count:
"why are we making dad harbor?": 250 words
"who are we?" 200 words
"what's the deal with the penguin logo?" 300 words

For the social media links, please see http://www.gravelplumbs.com/
Notice the floating "social" bar that is always to the right.  This is the concept we are going for, please try to implement this as you see fit. 

Target Market(s)

Fathers of young children ages 0-6 years old.

Industry/Entity Type

Product

Font styles to use
Sans Serif

Requirements
Must have
• Clean lines, minimal design concept

Incorporation of our logo (see attached document)

Header content is static for all views after landing page, see example

This page WILL be responsive, please keep that in mind when designing
The timeline bar should be to the left, with the timeline bar’s “milestones” also being responsive.

Designer is free to suggest font types, but any fonts used must be royalty-free and web-optimized. We request a minimum number of font types as well as fonts that load relatively fast. We reinforce that visually appealing typography is a significant factor in the winning design choice.

While we are not expecting the winning design to include code, please keep in mind that the final implementation needs to be optimized for desktop, tablet, and mobile platforms.

If you are using stock photography that is not generated by you, please provide where/how we can obtain imagery, as well as price.

All custom graphics must be available in original formats; Photoshop/GIMP layered files for layout design, and vector formats for logos, icons and other graphical elements.

Please incorporate “Blue” into design elements as you see fit, as the RGB 67 74 169 Blue is the primary color used in our brand. The complement to this blue is 255 202 0, a brownish orange. Feel free to use this color as well, although please keep it to a lesser amount.

Background color is your choice, do not feel the need to use the grey.
Should not have
• Excessive graphical content such that it affects loading times

Excessive use of too many font types such that it affects loading times

```html
<!DOCTYPE html>
<html lang="en">
<head>
<meta charset="utf-8">
<title>DadHarbor – Home</title>
<link href="https://fonts.googleapis.com/css2?family=Francois+One&family=Noto+Sans:wght@400;700&display=swap" rel="stylesheet">
<style>
:root{
  --brand-blue:#1e2f6e;
  --link-blue:#2a3a8c;
  --accent-orange:#f0a500;
  --header-top:#ffffff;
  --header-bottom:#e6e6e6;
  --panel-grey:#e6e6e6;
  --timeline-grey:#c9c9c9;
  --text-dark:#1b1b1b;
  --text-body:#444444;
  --white:#ffffff;
  --border-grey:#cfcfcf;
  --star-gold:#f2b61c;
  --star-grey:#cccccc;
  --marker-red:#e04a12;
  --grass:#6aa832;
  --share-bg:#f5f0dc;
  --share-circle:#3f4ca8;
}
*{box-sizing:border-box;margin:0;padding:0}
html,body{width:1019px;height:1200px;overflow:hidden;background:var(--white)}
body{position:relative;font-family:"Noto Sans",Arial,sans-serif;color:var(--text-dark)}
.abs{position:absolute}

/* header */
.site-header{position:absolute;left:0;top:0;width:1019px;height:118px;
  background:linear-gradient(var(--header-top),var(--header-bottom));
  border-bottom:3px solid var(--accent-orange)}
.brand{position:absolute;left:24px;top:22px;width:110px;text-align:center}
.brand-mark{width:46px;height:46px;border-radius:50%;background:var(--brand-blue);margin:0 auto 8px}
.brand-name{font-weight:700;font-size:14px;color:var(--brand-blue)}
.welcome{position:absolute;left:164px;top:10px;font-family:"Francois One",Arial,sans-serif;font-size:31px;font-weight:400;color:var(--text-dark);letter-spacing:.2px}
.score{position:absolute;left:164px;top:74px;font-size:14px}
.score b{color:var(--brand-blue)}
.search-field{position:absolute;left:372px;top:66px;width:255px;height:36px;background:var(--white);border:1px solid var(--border-grey);border-radius:3px}
.btn{position:absolute;height:37px;background:var(--brand-blue);color:var(--white);font-weight:700;font-size:14px;display:flex;align-items:center;justify-content:center;border-radius:3px;letter-spacing:.5px}
.btn-search{left:635px;top:65px;width:97px}
.btn-logout{left:899px;top:65px;width:96px}
.account{position:absolute;left:814px;top:74px;font-size:14px}

/* timeline */
.timeline-line{position:absolute;left:77px;top:121px;width:2px;height:1079px;background:var(--timeline-grey)}
.marker{position:absolute;left:10px;width:50px;height:68px}
.marker-stone{position:absolute;left:2px;top:0;width:46px;height:54px;background:linear-gradient(#fafafa,#dcdcdc);border-radius:23px 23px 4px 4px;border:1px solid #cfcfcf;text-align:center;font-size:17px;line-height:1;padding-top:15px;color:var(--text-dark)}
.marker-stone small{display:block;font-size:13px}
.marker-band{position:absolute;left:2px;top:54px;width:46px;height:12px;background:var(--marker-red);border-radius:0 0 3px 3px}
.marker-grass{position:absolute;left:-4px;top:58px;width:18px;height:8px;background:var(--grass);border-radius:8px 8px 0 0}
.toggle{position:absolute;left:66px;width:24px;height:24px;border-radius:50%;background:var(--white);border:1px solid #9a9a9a}
.toggle svg{display:block}

/* panels */
.panel{position:absolute;left:94px;width:901px;background:var(--panel-grey);border-radius:6px}
.panel-title{position:absolute;left:97px;font-size:18px;color:var(--text-dark)}
.task-list{position:absolute;left:112px;top:212px;width:223px;height:246px;background:var(--white);border:1px solid var(--border-grey);list-style:none;padding:12px 0 0 16px}
.task-list li{height:28px;display:flex;align-items:center;font-size:14px;color:#333}
.check{width:16px;height:16px;border:1px solid #cfcfcf;border-radius:3px;background:#eeeeee;margin-right:12px;flex:none}
.check.on{background:#d6e9fa;border-color:#7aa9d8}

.card{position:absolute;width:221px;height:278px;background:var(--white);padding:7px}
.card-media{width:206px;height:123px}
.media-photo{background:linear-gradient(135deg,#5c5149,#b08e6c 55%,#d7c3a8)}
.media-product{background:linear-gradient(#ffffff,#ffffff);display:flex;align-items:center;justify-content:center}
.media-product span{display:block;width:180px;height:90px;border-radius:40px;background:radial-gradient(#8f9670,#c6c9ad 60%,#fff 75%)}
.card-type{margin-top:14px;font-weight:700;font-size:14px;color:var(--link-blue)}
.card-meta{display:flex;justify-content:space-between;align-items:center;margin-top:6px;font-size:12px;color:#333}
.card-meta b{font-weight:400;color:var(--link-blue)}
.stars{display:flex;gap:1px}
.card-text{margin-top:12px;font-size:12px;line-height:16px;color:var(--text-body)}

.sort-label{position:absolute;left:858px;top:208px;font-size:12px}
.sort-select{position:absolute;left:858px;top:227px;width:98px;height:23px;background:var(--white);border:1px solid var(--border-grey);font-size:11px;padding:4px 6px;color:#333}
.sort-select i{position:absolute;right:7px;top:9px;border:5px solid transparent;border-top-color:var(--brand-blue)}

.share-bar{position:absolute;left:968px;top:181px;width:60px;height:219px;background:var(--share-bg);border:1px solid #c9c0a0;border-radius:6px 0 0 6px;padding-top:8px;text-align:left}
.share-bar p{font-size:12px;margin-left:12px;margin-bottom:6px}
.share-dot{width:40px;height:40px;border-radius:50%;background:var(--share-circle);margin:0 0 6px 8px}
</style>
</head>
<body>

<header class="site-header">
  <div class="brand"><div class="brand-mark"></div><div class="brand-name">DadHarbor</div></div>
  <h1 class="welcome">Welcome Greg, what would you like to do today?</h1>
  <p class="score">Super Dad Score: <b>10,500</b></p>
  <div class="search-field"></div>
  <div class="btn btn-search">SEARCH</div>
  <span class="account">My account</span>
  <div class="btn btn-logout">LOGOUT</div>
</header>

<div class="timeline-line"></div>

<!-- month 0, expanded -->
<section class="panel" style="top:164px;height:663px"></section>
<div class="marker" style="top:154px"><div class="marker-stone">0<small>mo</small></div><div class="marker-band"></div><div class="marker-grass"></div></div>
<div class="toggle" style="top:176px"><svg width="22" height="22"><path d="M6 11h10" stroke="#1e2f6e" stroke-width="2"/></svg></div>
<h2 class="panel-title" style="top:175px;font-weight:400">Prepare for the baby arrival</h2>

<ul class="task-list">
  <li><span class="check"></span>Buy a crib</li>
  <li><span class="check"></span>As semble the crib</li>
  <li><span class="check"></span>Buy a stroller</li>
  <li><span class="check on"><svg width="14" height="14"><path d="M3 7l3 3 6-7" stroke="#2a3a8c" stroke-width="2" fill="none"/></svg></span>Buy a carseat</li>
  <li><span class="check"></span>Install a carseat</li>
  <li><span class="check"></span>Learn to change a diaper</li>
  <li><span class="check"></span>Learn to hold a baby</li>
  <li><span class="check"></span>Set a feeding schedule</li>
</ul>

<svg width="0" height="0" style="position:absolute">
  <defs>
    <path id="star" d="M8 1l2.1 4.4 4.9.6-3.6 3.3.9 4.8L8 11.8 3.7 14.1l.9-4.8L1 6l4.9-.6z"/>
  </defs>
</svg>

<article class="card" style="left:360px;top:212px">
  <div class="card-media media-photo" role="img" aria-label="Photo of a father buckling a baby into a car seat"></div>
  <div class="card-type">ARTICLE</div>
  <div class="card-meta"><span class="stars"><svg width="80" height="16"><use href="#star" fill="#f2b61c"/><use href="#star" x="16" fill="#f2b61c"/><use href="#star" x="32" fill="#f2b61c"/><use href="#star" x="48" fill="#cccccc"/><use href="#star" x="64" fill="#cccccc"/></svg></span><span><b>3,121</b> ratings</span></div>
  <p class="card-text">I went out to buy my first car seat and had to earn my PhD in car seats, Newtonian physics, and anti-stain technology…</p>
</article>

<article class="card" style="left:613px;top:212px">
  <div class="card-media media-product" role="img" aria-label="Product photo of a green stroller and matching infant carrier"><span></span></div>
  <div class="card-type">PRODUCT</div>
  <div class="card-meta"><span class="stars"><svg width="80" height="16"><use href="#star" fill="#f2b61c"/><use href="#star" x="16" fill="#f2b61c"/><use href="#star" x="32" fill="#f2b61c"/><use href="#star" x="48" fill="#cccccc"/><use href="#star" x="64" fill="#cccccc"/></svg></span><span><b>9,102</b> likes</span></div>
  <p class="card-text">The Ravello XT stroller is this year’s hottest stroller, for more reasons than are obvious. What we particularly like about it is…</p>
</article>

<article class="card" style="left:360px;top:515px">
  <div class="card-media media-photo" role="img" aria-label="Photo of a father buckling a baby into a car seat"></div>
  <div class="card-type">ARTICLE</div>
  <div class="card-meta"><span class="stars"><svg width="80" height="16"><use href="#star" fill="#f2b61c"/><use href="#star" x="16" fill="#f2b61c"/><use href="#star" x="32" fill="#f2b61c"/><use href="#star" x="48" fill="#cccccc"/><use href="#star" x="64" fill="#cccccc"/></svg></span><span><b>1,595</b> likes</span></div>
  <p class="card-text">I learned something new this week which made my penny-pinching side just giddy. Car seats double as airplane…</p>
</article>

<article class="card" style="left:613px;top:515px">
  <div class="card-media media-photo" role="img" aria-label="Photo of a father buckling a baby into a car seat"></div>
  <div class="card-type">ARTICLE</div>
  <div class="card-meta"><span class="stars"><svg width="80" height="16"><use href="#star" fill="#f2b61c"/><use href="#star" x="16" fill="#f2b61c"/><use href="#star" x="32" fill="#f2b61c"/><use href="#star" x="48" fill="#cccccc"/><use href="#star" x="64" fill="#cccccc"/></svg></span><span><b>9,007</b> likes</span></div>
  <p class="card-text">Don’t forget your go-bag essentials! Camping gear aside, Trailmate Co has assembled a great kit to take…</p>
</article>

<span class="sort-label">Sort by:</span>
<div class="sort-select">Most recent<i></i></div>

<aside class="share-bar">
  <p>Share</p>
  <div class="share-dot"></div>
  <div class="share-dot"></div>
  <div class="share-dot"></div>
  <div class="share-dot"></div>
</aside>

<!-- month 1 -->
<section class="panel" style="top:858px;height:50px"></section>
<div class="marker" style="top:850px"><div class="marker-stone">1<small>mo</small></div><div class="marker-band"></div><div class="marker-grass"></div></div>
<div class="toggle" style="top:871px"><svg width="22" height="22"><path d="M6 11h10M11 6v10" stroke="#1e2f6e" stroke-width="2"/></svg></div>
<h2 class="panel-title" style="top:871px;font-weight:400">Prepare for the baby arrival</h2>

<!-- month 2 -->
<section class="panel" style="top:942px;height:50px"></section>
<div class="marker" style="top:933px"><div class="marker-stone">2<small>mo</small></div><div class="marker-band"></div><div class="marker-grass"></div></div>
<div class="toggle" style="top:955px"><svg width="22" height="22"><path d="M6 11h10M11 6v10" stroke="#1e2f6e" stroke-width="2"/></svg></div>
<h2 class="panel-title" style="top:954px;font-weight:400">Prepare for the baby arrival</h2>

<!-- month 3 -->
<section class="panel" style="top:1024px;height:51px"></section>
<div class="marker" style="top:1016px"><div class="marker-stone">3<small>mo</small></div><div class="marker-band"></div><div class="marker-grass"></div></div>
<div class="toggle" style="top:1038px"><svg width="22" height="22"><path d="M6 11h10M11 6v10" stroke="#1e2f6e" stroke-width="2"/></svg></div>
<h2 class="panel-title" style="top:1037px;font-weight:400">What’s the latest?</h2>

<!-- month 4 -->
<section class="panel" style="top:1115px;height:51px"></section>
<div class="marker" style="top:1107px"><div class="marker-stone">4<small>mo</small></div><div class="marker-band"></div><div class="marker-grass"></div></div>
<div class="toggle" style="top:1129px"><svg width="22" height="22"><path d="M6 11h10M11 6v10" stroke="#1e2f6e" stroke-width="2"/></svg></div>
<h2 class="panel-title" style="top:1128px;font-weight:400">What you searched for:</h2>

</body>
</html>
```